Automotive Accessories Business Card

Design a business template that match our new logo design and our industry.

https://www.qelmotorgear.com/

Target Market(s)

Aftermarket auto parts and accessories

Industry/Entity Type

automotive

Contact Information for Business Card

company logo

Font styles to use
Serif
Sans Serif

Colors
EB3D1F
EC4F4E
F09395
F8D3D4
FCEDEE

```html
<!DOCTYPE html>
<html lang="en">
<head>
<meta charset="utf-8">
<title>QEL Motor Gear – Business Card</title>
<link href="https://fonts.googleapis.com/css2?family=Open+Sans:wght@400;600;800&display=swap" rel="stylesheet">
<style>
  :root {
    --red: #e0313a;
    --red-deep: #b8161d;
    --charcoal: #3b3b3d;
    --charcoal-soft: #4a4a4c;
    --ink: #3a3a3c;
    --paper: #f6f6f6;
    --stage: #e8e6e3;
    --rule: #4a4a4a;
  }
  * { box-sizing: border-box; margin: 0; padding: 0; }
  html, body {
    width: 1200px; height: 960px; overflow: hidden;
    background: var(--stage);
    font-family: "Open Sans", Arial, sans-serif;
  }
  .card {
    position: absolute; left: 250px; width: 700px; height: 400px;
    overflow: hidden;
    box-shadow: 0 10px 28px rgba(0,0,0,.18);
  }
  /* Front */
  .card-front { top: 40px; background: linear-gradient(135deg, #ffffff 0%, var(--paper) 60%, #ececec 100%); }
  .brand {
    position: absolute; left: 0; right: 0; top: 92px;
    display: flex; align-items: center; justify-content: center; gap: 14px;
  }
  .brand-mark { width: 22px; height: 22px; background: var(--red); }
  .brand-name {
    font-weight: 800; font-size: 40px; letter-spacing: 1px;
    color: var(--red); line-height: 1;
  }
  .front-rule {
    position: absolute; left: 60px; right: 60px; top: 200px;
    height: 2px; background: var(--rule);
  }
  .holder {
    position: absolute; top: 232px; left: 60px; width: 220px;
    text-align: right;
  }
  .holder-name { font-weight: 800; font-size: 26px; color: var(--ink); letter-spacing: .5px; }
  .holder-title { font-weight: 400; font-size: 18px; color: var(--ink); margin-top: 2px; }
  .divider {
    position: absolute; left: 300px; top: 228px; width: 2px; height: 98px;
    background: var(--rule);
  }
  .contacts {
    position: absolute; left: 322px; top: 228px;
    list-style: none; font-size: 19px; color: var(--ink);
  }
  .contacts li { display: flex; align-items: center; gap: 10px; height: 32px; }
  .contacts svg { width: 20px; height: 20px; flex: none; }
  .contacts .accent { color: var(--red); font-weight: 600; }
  .front-band {
    position: absolute; left: 0; right: 0; bottom: 0; height: 22px;
    background: var(--charcoal);
  }
  .band-flag {
    position: absolute; left: 14px; bottom: 22px; width: 56px; height: 22px;
    background: linear-gradient(90deg, var(--charcoal-soft), var(--red));
  }
  /* Back */
  .card-back { top: 500px; background: var(--charcoal); }
  .back-field {
    position: absolute; left: 0; top: 110px; width: 540px; height: 290px;
    background: linear-gradient(135deg, #f4f4f4 0%, var(--red) 45%, var(--charcoal-soft) 75%, var(--red-deep) 100%);
    opacity: .9;
  }
  .card-back .brand { left: auto; right: 40px; top: 70px; justify-content: flex-end; }
  .card-back .brand-name { color: #ffffff; font-size: 34px; }
</style>
</head>
<body>

<section class="card card-front" aria-label="Business card front">
  <div class="brand">
    <span class="brand-mark"></span>
    <span class="brand-name">QEL MOTOR GEAR</span>
  </div>
  <div class="front-rule"></div>

  <div class="holder">
    <div class="holder-name">MARCO ELLISON</div>
    <div class="holder-title">Sales Manager</div>
  </div>
  <div class="divider"></div>

  <ul class="contacts">
    <li>
      <svg viewBox="0 0 24 24" aria-hidden="true"><path fill="var(--red)" d="M6.6 10.8a15.1 15.1 0 0 0 6.6 6.6l2.2-2.2a1 1 0 0 1 1-.25 11.4 11.4 0 0 0 3.6.57 1 1 0 0 1 1 1V20a1 1 0 0 1-1 1A17 17 0 0 1 3 4a1 1 0 0 1 1-1h3.5a1 1 0 0 1 1 1c0 1.25.2 2.45.57 3.6a1 1 0 0 1-.25 1z"/></svg>
      <span>1-866-555-0142</span>
    </li>
    <li>
      <svg viewBox="0 0 24 24" aria-hidden="true"><path fill="var(--red)" d="M2 5h20v14H2z"/><path fill="none" stroke="#fff" stroke-width="1.6" d="M2.5 5.5 12 13l9.5-7.5"/></svg>
      <span>sales@qelmotorgear.com</span>
    </li>
    <li>
      <svg viewBox="0 0 24 24" aria-hidden="true"><circle cx="12" cy="12" r="10" fill="var(--red)"/><g fill="none" stroke="#fff" stroke-width="1.3"><ellipse cx="12" cy="12" rx="4.5" ry="10"/><path d="M2 12h20M4 7h16M4 17h16"/></g></svg>
      <span>www.<span class="accent">qelmotorgear</span>.com</span>
    </li>
  </ul>

  <div class="band-flag" role="img" aria-label="Small racing flag accent"></div>
  <div class="front-band"></div>
</section>

<section class="card card-back" aria-label="Business card back">
  <div class="back-field" role="img" aria-label="Large red, white and charcoal racing check field"></div>
  <div class="brand">
    <span class="brand-mark"></span>
    <span class="brand-name">QEL MOTOR GEAR</span>
  </div>
</section>

</body>
</html>
```